Pelican HVAC WordPress website design

Design a new modern, clean, website for HVAC mechanical business that uses company logo/colors for branding and recognition. Files attached are just for band and color information. Here is a website design that appeals to me https://www.corvellsupply.example/

A clear description of who we are and what we do

An easily-navigated site map

An easily-navigated site map for mobile devices

Easy-to-find contact information

Obvious call to action for service, installs or to schedule estimates

about us page

Provide a way for potential customers to contact us via text or email

provide a way that allows a customer to upload a picture to request a service call or quote.
Updates

I'm looking for the design to be completed in WordPress

Industry/Entity Type

HVAC Mechanical & Building Automation / Controls contractor

Coding

Coded - Design and coding required

Number of Pages Required

5+ page

Colors
0054AA
0677BA
7BADD7
CADEEF
E8F1F8

Requirements
Must have
• Design a new modern, clean, website for HVAC mechanical business that uses company logo/colors for branding and recognition. Files attached are just for band and color information. Here is a website design that appeals to me https://www.corvellsupply.example/ A clear description of who we are and what we do An easily-navigated site map An easily-navigated site map for mobile devices Easy-to-find contact information Obvious call to action for service, installs or to schedule estimates about us page Provide a way for potential customers to contact us via text or email provide a way that allows a customer to upload a picture to request a service call or quote.
Nice to have

```html
<!DOCTYPE html>
<html lang="en">
<head>
<meta charset="utf-8">
<title>Pelican HVAC</title>
<link href="https://fonts.googleapis.com/css2?family=Roboto+Slab:wght@300;400;500;600;700&display=swap" rel="stylesheet">
<style>
:root{
  --blue:#0054AA;
  --blue-2:#0677BA;
  --blue-3:#7BADD7;
  --blue-4:#CADEEF;
  --blue-5:#E8F1F8;
  --navy:#1f3f86;
  --dark:#333333;
  --ink:#2b2b2b;
  --text:#444444;
  --black:#000000;
  --white:#ffffff;
}
*{margin:0;padding:0;box-sizing:border-box}
html,body{width:1200px;height:3994px;overflow:hidden}
body{font-family:"Roboto Slab",serif;color:var(--text);background:var(--white);position:relative}
.abs{position:absolute}
.btn{display:inline-block;background:var(--blue);color:var(--white);font-size:15px;padding:11px 21px;text-decoration:none}
.photo{position:absolute}

.header{position:absolute;left:0;top:0;width:1200px;height:162px}
.topbar{position:absolute;left:372px;top:0;width:828px;height:42px;background:var(--blue);clip-path:polygon(0 0,100% 0,100% 100%,38px 100%)}
.topbar .welcome{position:absolute;left:60px;top:13px;color:var(--white);font-size:13px;white-space:nowrap}
.topbar .estimate{position:absolute;left:538px;top:0;height:42px;width:176px;background:var(--dark);color:var(--white);font-size:15px;line-height:42px;text-align:center}
.logo{position:absolute;left:112px;top:20px;width:232px;height:122px;display:flex;align-items:center;gap:12px}
.logo .dot{width:40px;height:40px;border-radius:50%;background:var(--blue)}
.logo span{font-size:28px;font-weight:700;color:var(--blue)}
.contact-item{position:absolute;top:56px;display:flex;gap:10px}
.contact-item svg{margin-top:6px}
.contact-item b{display:block;font-weight:500;font-size:17px;color:var(--ink)}
.contact-item small{display:block;font-size:13px;color:var(--text);margin-top:3px;white-space:nowrap}
.navbar{position:absolute;left:372px;top:120px;width:828px;height:42px;background:var(--dark);clip-path:polygon(38px 0,100% 0,100% 100%,0 100%)}
.navbar ul{list-style:none;position:absolute;left:44px;top:0;display:flex}
.navbar li{color:var(--white);font-size:13px;line-height:42px;padding:0 19px}
.navbar li.active{background:var(--blue)}
.navbar svg{position:absolute;right:124px;top:13px}

.hero{position:absolute;left:0;top:162px;width:1200px;height:600px;background:linear-gradient(90deg,#4c5766,#6a6c6a 40%,#56606c 70%,#3d4a5c);text-align:center;color:var(--white)}
.hero .shade{position:absolute;inset:0;background:rgba(20,40,80,.35)}
.hero .inner{position:relative;padding-top:154px}
.hero .sub{font-size:44px;font-weight:300}
.hero h1{font-size:80px;font-weight:700;line-height:1;margin-top:6px}
.hero p{font-size:21px;font-weight:500;width:520px;margin:28px auto 0;line-height:1.45}
.hero .btn{margin-top:26px;font-size:15px;padding:12px 24px}

.who-photo{left:112px;top:848px;width:428px;height:429px;background:linear-gradient(135deg,#cfd6d8,#6f9a9f 50%,#3f5e6a)}
.who{position:absolute;left:613px;top:848px;width:476px}
.who h2{font-size:40px;font-weight:500;color:var(--ink)}
.who p{font-size:15px;line-height:1.72;margin-top:22px}
.who .btn{margin-top:30px}

.stats{position:absolute;left:0;top:1363px;width:1200px;height:222px;background:linear-gradient(90deg,#1a6cb4,#2a79b9 50%,#1866ad);display:flex;justify-content:space-around;padding:0 46px;color:var(--white);text-align:center}
.stat{width:200px;padding-top:54px}
.stat b{display:block;font-size:19px;font-weight:600;margin-top:8px}
.stat span{display:block;font-size:19px;font-weight:600;margin-top:2px}

.title{position:absolute;left:0;width:1200px;text-align:center;font-size:40px;font-weight:500;color:var(--ink)}

.arrow{position:absolute;width:36px;height:36px;border-radius:50%;background:var(--ink);display:flex;align-items:center;justify-content:center}
.card{position:absolute;top:1738px;width:310px;height:460px;background:var(--white);box-shadow:0 0 8px rgba(0,0,0,.18);text-align:center}
.card .pic{margin:9px;height:195px}
.card h3{font-size:21px;font-weight:600;color:var(--blue);margin-top:20px}
.card p{font-size:15px;line-height:1.72;width:250px;margin:14px auto 0}
.card .btn{margin-top:24px}

.testi{position:absolute;left:0;top:2284px;width:1200px;height:439px;background:linear-gradient(90deg,#233f86,#203f8a 60%,#1d3a80);color:var(--white);text-align:center}
.testi h2{font-size:40px;font-weight:600;margin-top:64px}
.testi .who-line{display:flex;justify-content:center;align-items:center;gap:22px;margin-top:28px;text-align:left}
.avatar{width:86px;height:86px;border-radius:50%;border:3px solid var(--white);background:linear-gradient(#c9d3dc,#8aa0b6)}
.testi .name{font-size:21px;font-weight:600}
.testi .role{font-size:15px;margin-top:6px}
.testi .quote{font-size:17px;line-height:1.55;width:640px;margin:28px auto 0}
.dots{display:flex;justify-content:center;gap:5px;margin-top:14px}
.dots i{display:block;height:6px;background:var(--white);border-radius:3px}

.post{position:absolute;top:2884px;width:302px;height:414px;background:var(--white);box-shadow:0 0 8px rgba(0,0,0,.15)}
.post .pic{height:207px}
.post .date{position:absolute;left:-6px;top:170px;width:46px;height:38px;background:var(--navy);color:var(--white);font-size:13px;line-height:1.1;text-align:center;padding-top:5px}
.post h3{font-size:20px;font-weight:500;color:var(--ink);margin:38px 0 0 30px}
.post p{font-size:15px;line-height:1.5;margin:12px 20px 0 30px}
.post a{display:block;font-size:15px;font-weight:600;color:var(--blue);margin:10px 0 0 30px;text-decoration:none}

.footer{position:absolute;left:0;top:3522px;width:1200px;height:433px;background:var(--black);color:var(--white)}
.request{position:absolute;left:112px;top:3385px;width:976px;height:180px;background:var(--blue);text-align:center;z-index:2}
.request h2{color:var(--white);font-size:38px;font-weight:600;margin-top:26px}
.form{display:flex;gap:15px;justify-content:center;margin-top:24px}
.field{width:166px;height:34px;background:var(--white);font-size:13px;color:#555;text-align:left;padding:9px 16px;position:relative}
.field svg{position:absolute;right:12px;top:10px}
.submit{width:152px;height:36px;background:var(--dark);color:var(--white);font-size:15px;line-height:36px;margin-left:2px}
.flogo{left:112px;top:3700px;width:232px;height:122px;display:flex;align-items:center;gap:12px}
.flogo .dot{width:40px;height:40px;border-radius:50%;background:var(--blue-3)}
.flogo span{font-size:28px;font-weight:700;color:var(--blue-4)}
.fcol h4{font-size:21px;font-weight:600}
.fcol ul{list-style:none;margin-top:18px}
.fcol li{font-size:13px;margin-bottom:11px}
.fc-item{display:flex;gap:12px;margin-top:12px}
.fc-item b{display:block;font-size:17px;font-weight:500}
.fc-item small{display:block;font-size:13px;line-height:1.6}
.social{display:flex;align-items:center;gap:18px;margin-top:22px;font-size:14px}
.social i{display:block;width:22px;height:22px;border:2px solid var(--white)}
.copyright{position:absolute;left:0;top:3955px;width:1200px;height:39px;background:var(--navy);color:var(--white);font-size:14px;text-align:center;line-height:39px}
</style>
</head>
<body>

<header class="header">
  <div class="logo"><div class="dot"></div><span>Pelican HVAC</span></div>
  <div class="topbar">
    <div class="welcome">Welcome&nbsp; to Pelican HVAC Mechanical Business .</div>
    <div class="estimate">Schedule Estimates</div>
  </div>
  <div class="contact-item" style="left:404px">
    <svg width="14" height="18" viewBox="0 0 14 18"><path d="M7 0a7 7 0 0 1 7 7c0 5-7 11-7 11S0 12 0 7a7 7 0 0 1 7-7z" fill="#0054AA"/><circle cx="7" cy="7" r="2.6" fill="#fff"/></svg>
    <div><b>Address</b><small>123,Pelican HVAC Company.504218</small></div>
  </div>
  <div class="contact-item" style="left:728px">
    <svg width="14" height="14" viewBox="0 0 24 24"><path d="M6.6 10.8a15 15 0 0 0 6.6 6.6l2.2-2.2a1 1 0 0 1 1-.25 11 11 0 0 0 3.6.6 1 1 0 0 1 1 1V20a1 1 0 0 1-1 1A17 17 0 0 1 3 4a1 1 0 0 1 1-1h3.5a1 1 0 0 1 1 1 11 11 0 0 0 .6 3.6 1 1 0 0 1-.25 1z" fill="#0054AA"/></svg>
    <div><b>Phone</b><small>603-555-0142</small></div>
  </div>
  <div class="contact-item" style="left:914px">
    <svg width="15" height="11" viewBox="0 0 15 11"><rect width="15" height="11" fill="#0054AA"/><path d="M0 0l7.5 6L15 0" stroke="#fff" stroke-width="1.4" fill="none"/></svg>
    <div><b>Email</b><small>info@pelicanhvac.example</small></div>
  </div>
  <nav class="navbar">
    <ul>
      <li class="active">Home</li><li>About Us</li><li>what we do</li><li>Services</li><li>Blog</li><li>Contact Us</li>
    </ul>
    <svg width="16" height="16" viewBox="0 0 16 16"><circle cx="6.5" cy="6.5" r="5" stroke="#fff" stroke-width="1.8" fill="none"/><path d="M10.5 10.5L15 15" stroke="#fff" stroke-width="1.8"/></svg>
  </nav>
</header>

<section class="hero">
  <div class="shade" role="img" aria-label="Two HVAC technicians in caps working with tools and a phone outdoors"></div>
  <div class="inner">
    <div class="sub">Welcome To</div>
    <h1>Pelican HVAC</h1>
    <p>Excepteur sint occaecat cupidatat non,in culpa qui officia laborum.</p>
    <a class="btn" href="#">Request&nbsp; A Services</a>
  </div>
</section>

<div class="photo who-photo" role="img" aria-label="Technicians servicing a wall-mounted air conditioning unit"></div>
<section class="who">
  <h2>Who We Are</h2>
  <p>Lorem ipsum dolor sit amet, consectetur adipiscing elit, sed do eiusmod tempor incididunt ut labore et dolore magna aliqua. Ut enim ad minim veniam, quis nostrud exercitation ullamco laboris nisi ut aliquip ex ea commodo consequat. Duis aute irure dolor in reprehenderit in voluptate velit esse cillum dolore eu fugiat nulla pariatur.</p>
  <p>Sed ut perspiciatis unde omnis iste natus error sit voluptatem accusantium doloremque laudantium, totam rem aperiam, eaque ipsa quae ab illo inventore veritatis et quasi architecto beatae vitae dicta sunt explicabo.</p>
  <a class="btn" href="#">Read More</a>
</section>

<section class="stats">
  <div class="stat">
    <svg width="50" height="48" viewBox="0 0 50 48" fill="#fff"><circle cx="25" cy="14" r="7"/><path d="M13 40c0-9 5-14 12-14s12 5 12 14z"/><circle cx="10" cy="20" r="5"/><path d="M1 42c0-7 4-11 9-11s6 2 6 4l-3 7z"/><circle cx="40" cy="20" r="5"/><path d="M49 42c0-7-4-11-9-11s-6 2-6 4l3 7z"/><path d="M25 0l2 4 4 .5-3 3 .8 4-3.8-2-3.8 2 .8-4-3-3 4-.5z"/></svg>
    <b>200</b><span>Total Experts</span>
  </div>
  <div class="stat">
    <svg width="48" height="48" viewBox="0 0 48 48"><circle cx="24" cy="24" r="17" fill="none" stroke="#fff" stroke-width="8" stroke-dasharray="6 4.6"/><circle cx="24" cy="24" r="12" fill="#fff"/><path d="M18 24l4 4 8-8" stroke="#1a6cb4" stroke-width="3" fill="none"/></svg>
    <b>250</b><span>Service Done</span>
  </div>
  <div class="stat">
    <svg width="50" height="50" viewBox="0 0 50 50"><circle cx="25" cy="25" r="22" fill="none" stroke="#fff" stroke-width="3"/><circle cx="25" cy="19" r="8" fill="#fff"/><path d="M11 40c2-9 8-12 14-12s12 3 14 12" fill="#fff"/></svg>
    <b>200</b><span>Happy Client</span>
  </div>
  <div class="stat">
    <svg width="50" height="50" viewBox="0 0 50 50"><circle cx="25" cy="25" r="17" fill="none" stroke="#fff" stroke-width="8" stroke-dasharray="6 4.6"/><circle cx="25" cy="25" r="8" fill="#1a6cb4" stroke="#fff" stroke-width="3"/><path d="M30 30l12 12" stroke="#fff" stroke-width="6" stroke-linecap="round"/></svg>
    <b>300</b><span>Total Service</span>
  </div>
</section>

<h2 class="title" style="top:1662px">What We Do</h2>
<div class="arrow" style="left:53px;top:1935px"><svg width="12" height="14" viewBox="0 0 12 14"><path d="M9 1L3 7l6 6" stroke="#fff" stroke-width="2.5" fill="none"/></svg></div>
<div class="arrow" style="left:1111px;top:1935px"><svg width="12" height="14" viewBox="0 0 12 14"><path d="M3 1l6 6-6 6" stroke="#fff" stroke-width="2.5" fill="none"/></svg></div>
<div class="card" style="left:110px">
  <div class="pic" role="img" aria-label="Technician installing an air conditioner in a kitchen" style="background:linear-gradient(135deg,#e6e2dc,#8a7b6c)"></div>
  <h3>Air Conditioning</h3>
  <p>Duis aute irure dolor in reprehenderit in voluptate velit cillum dolore eu fugiat nulla pariatur.</p>
  <a class="btn" href="#">Read More</a>
</div>
<div class="card" style="left:443px">
  <div class="pic" role="img" aria-label="Gloved hand adjusting a white heating radiator" style="background:linear-gradient(135deg,#e9ecef,#9aa7b5 60%,#3b5f9a)"></div>
  <h3>Heating</h3>
  <p>Duis aute irure dolor in reprehenderit in voluptate velit cillum dolore eu fugiat nulla pariatur.</p>
  <a class="btn" href="#">Read More</a>
</div>
<div class="card" style="left:775px">
  <div class="pic" role="img" aria-label="Technician in red servicing an outdoor heat pump near solar panels" style="background:linear-gradient(135deg,#8fb0d8,#4b5a73 50%,#c43a34)"></div>
  <h3>Heat Pumps</h3>
  <p>Duis aute irure dolor in reprehenderit in voluptate velit cillum dolore eu fugiat nulla pariatur.</p>
  <a class="btn" href="#">Read More</a>
</div>

<section class="testi">
  <h2>Testimonials</h2>
  <div class="who-line">
    <div class="avatar" role="img" aria-label="Customer portrait"></div>
    <div><div class="name">Lorem ipsum dolor</div><div class="role">Customer</div></div>
  </div>
  <p class="quote">"Sed ut perspiciatis unde omnis iste natus error sit voluptatem accusantium doloremque laudantium, totam rem aperiam, eaque ipsa quae ab illo inventore veritatis et quasi architecto beatae vitae dicta sunt explicabo.</p>
  <div class="dots"><i style="width:24px"></i><i style="width:6px"></i></div>
</section>

<h2 class="title" style="top:2800px">Our Blog</h2>
<div class="arrow" style="left:53px;top:3056px"><svg width="12" height="14" viewBox="0 0 12 14"><path d="M9 1L3 7l6 6" stroke="#fff" stroke-width="2.5" fill="none"/></svg></div>
<div class="arrow" style="left:1111px;top:3056px"><svg width="12" height="14" viewBox="0 0 12 14"><path d="M3 1l6 6-6 6" stroke="#fff" stroke-width="2.5" fill="none"/></svg></div>
<article class="post" style="left:118px">
  <div class="pic" role="img" aria-label="Plumber working on an orange boiler and pipes" style="background:linear-gradient(135deg,#9aa0a6,#d65a22 55%,#3a3a3a)"></div>
  <div class="date">01<br>Feb</div>
  <h3>Lorem ipsum dolor</h3>
  <p>Excepteur sint occaecat cupidatat non proident, sunt in culpa qui officia deserunt mollit anim id est</p>
  <a href="#">Read More.....</a>
</article>
<article class="post" style="left:451px">
  <div class="pic" role="img" aria-label="Technician in red gloves repairing a furnace control board" style="background:linear-gradient(135deg,#5f7fa6,#cfd6dc 55%,#2f5e9e)"></div>
  <div class="date">01<br>Feb</div>
  <h3>Lorem ipsum dolor</h3>
  <p>Excepteur sint occaecat cupidatat non proident, sunt in culpa qui officia deserunt mollit anim id est</p>
  <a href="#">Read More.....</a>
</article>
<article class="post" style="left:784px">
  <div class="pic" role="img" aria-label="Engineer in hard hat checking a tablet in a boiler room" style="background:linear-gradient(135deg,#b9bcbf,#e2e2e0 55%,#6c7178)"></div>
  <div class="date">01<br>Feb</div>
  <h3>Lorem ipsum dolor</h3>
  <p>Excepteur sint occaecat cupidatat non proident, sunt in culpa qui officia deserunt mollit anim id est</p>
  <a href="#">Read More.....</a>
</article>

<section class="request">
  <h2>Request A Service Call</h2>
  <div class="form">
    <div class="field">Your Name</div>
    <div class="field">Your E-mail</div>
    <div class="field">Your Phone</div>
    <div class="field">Upload Picture
      <svg width="14" height="13" viewBox="0 0 14 13"><path d="M7 0v8M3.5 4.5L7 8l3.5-3.5M1 9v3h12V9" stroke="#333" stroke-width="1.8" fill="none"/></svg>
    </div>
    <div class="submit">Submit</div>
  </div>
</section>

<footer class="footer"></footer>
<div class="abs flogo"><div class="dot"></div><span>Pelican HVAC</span></div>
<div class="abs fcol" style="left:440px;top:3666px;color:#fff">
  <h4>Quick Links</h4>
  <ul><li>Home</li><li>About Us</li><li>what we do</li><li>Services</li><li>Blog</li><li>Contact Us</li></ul>
</div>
<div class="abs fcol" style="left:675px;top:3666px;color:#fff">
  <h4>Contact Details</h4>
  <div class="fc-item" style="margin-top:16px"><svg width="12" height="16" viewBox="0 0 14 18"><path d="M7 0a7 7 0 0 1 7 7c0 5-7 11-7 11S0 12 0 7a7 7 0 0 1 7-7z" fill="#fff"/><circle cx="7" cy="7" r="2.6" fill="#000"/></svg><div><b>Address</b><small>123,Pelican HVAC<br>Company.504218</small></div></div>
  <div class="fc-item"><svg width="13" height="13" viewBox="0 0 24 24"><path d="M6.6 10.8a15 15 0 0 0 6.6 6.6l2.2-2.2a1 1 0 0 1 1-.25 11 11 0 0 0 3.6.6 1 1 0 0 1 1 1V20a1 1 0 0 1-1 1A17 17 0 0 1 3 4a1 1 0 0 1 1-1h3.5a1 1 0 0 1 1 1 11 11 0 0 0 .6 3.6 1 1 0 0 1-.25 1z" fill="#fff"/></svg><div><b>Phone</b><small>603-555-0142</small></div></div>
  <div class="fc-item"><svg width="14" height="10" viewBox="0 0 15 11"><rect width="15" height="11" fill="#fff"/><path d="M0 0l7.5 6L15 0" stroke="#000" stroke-width="1.4" fill="none"/></svg><div><b>Email</b><small>info@pelicanhvac.example</small></div></div>
</div>
<div class="abs fcol" style="left:982px;top:3666px;color:#fff">
  <h4>Follow Us</h4>
  <div class="social"><i></i>Social One</div>
  <div class="social"><i></i>Social Two</div>
  <div class="social"><i></i>Social Three</div>
</div>
<div class="copyright">Copyright &nbsp;© 2024. Pelican HVAC .All Rights Reserved.</div>

</body>
</html>
```